Automotive component supplier needs a business card design

We need a business card design for our company called Velran Global Components Ltd based in the UK. We are a supplier of interior and exterior components to premium car manufacturers such as Corvel Ashby, Hadley Fenn, Marquist and Tavarelli. We would like to see a modern business card design that uses the colour blue.

Target Market(s)

Premium automotive car manufacturers.

Industry/Entity Type

Automotive

Contact Information for Business Card

Company Name : Velran Global Components Limited
Address: 17 Marlow Yard, Upper Heath, Warwick, CV31 8QL, United Kingdom
Web Address : www.velrancomponents-example.co.uk

Font styles to use
Other font styles liked:
• Helvetica

Colors
3176b5
0255a3
85acd3
cfdeed
cee9f5
85cae6
34a6d7
0692cd
9bcb3c

Requirements
Must have
• Clear company logo and a mixture of blue colours.
Nice to have
• A high quality modern image.
Should not have
• Multiple colours.

```html
<!DOCTYPE html>
<html lang="en">
<head>
<meta charset="utf-8">
<title>Velran Global Components – Business Card</title>
<link rel="stylesheet" href="https://fonts.googleapis.com/css2?family=Lato:wght@400;700&display=swap">
<style>
  :root {
    --brand-blue: #0a8acb;
    --deep-blue: #0673b0;
    --accent-green: #9bcb3c;
    --paper: #ffffff;
    --backdrop: #e6e9ec;
    --card-w: 620px;
    --card-h: 354px;
  }
  * { box-sizing: border-box; margin: 0; padding: 0; }
  html, body {
    width: 1200px; height: 800px; overflow: hidden;
    background: var(--backdrop);
    font-family: "Lato", Helvetica, Arial, sans-serif;
  }
  .sheet { position: relative; width: 1200px; height: 800px; }
  .card {
    position: absolute; left: 290px;
    width: var(--card-w); height: var(--card-h);
    overflow: hidden;
    box-shadow: 0 6px 18px rgba(0,0,0,.18);
  }
  .card--back { top: 36px; background: var(--brand-blue); }
  .card--front { top: 410px; background: var(--brand-blue); }

  .wordmark {
    display: flex; align-items: center; gap: 12px;
    font-weight: 700; font-size: 34px; letter-spacing: .5px;
    white-space: nowrap;
  }
  .wordmark__square {
    width: 16px; height: 16px; background: var(--accent-green); flex: none;
  }
  .card--back .wordmark {
    position: absolute; left: 0; right: 0; top: 128px;
    justify-content: center; color: var(--paper);
  }
  .card--back .web {
    position: absolute; left: 0; right: 0; bottom: 52px;
    text-align: center; color: var(--paper);
    font-size: 15px; letter-spacing: 1.5px;
  }

  .front-art { position: absolute; inset: 0; width: 100%; height: 100%; }
  .card--front .wordmark {
    position: absolute; left: 32px; top: 78px;
    color: var(--brand-blue); font-size: 27px; gap: 10px;
  }
  .card--front .wordmark__square { width: 14px; height: 14px; }
  .address {
    position: absolute; left: 40px; bottom: 30px;
    color: var(--paper); font-size: 16px; line-height: 1.35;
    font-style: normal;
  }
  .contact {
    position: absolute; right: 32px; top: 172px;
    text-align: right; color: var(--paper);
  }
  .contact__name {
    color: var(--accent-green); font-weight: 700; font-size: 21px; line-height: 1.15;
  }
  .contact__role { font-size: 14px; margin-bottom: 10px; }
  .contact__line {
    display: flex; justify-content: flex-end; align-items: center;
    gap: 9px; font-size: 15px; line-height: 1.4;
  }
  .contact__icon { width: 12px; height: 12px; flex: none; }
</style>
</head>
<body>
<main class="sheet">

  <section class="card card--back" aria-label="Business card back">
    <div class="wordmark"><span class="wordmark__square"></span>Velran Global Components</div>
    <p class="web">www.velrancomponents-example.co.uk</p>
  </section>

  <section class="card card--front" aria-label="Business card front">
    <svg class="front-art" viewBox="0 0 620 354" preserveAspectRatio="none" aria-hidden="true">
      <path d="M0,0 H505 C460,140 320,222 0,236 Z" fill="#ffffff"/>
      <path d="M512,0 H526 C480,130 390,185 300,215 C385,178 470,120 512,0 Z" fill="#9bcb3c"/>
    </svg>

    <div class="wordmark"><span class="wordmark__square"></span>Velran Global Components</div>

    <div class="contact">
      <p class="contact__name">Marcus Telford</p>
      <p class="contact__role">Manager</p>
      <p class="contact__line">512 004 3720
        <svg class="contact__icon" viewBox="0 0 12 12"><path d="M2.5 1 L4.5 1 L5 3.5 L3.8 4.4 C4.4 6 6 7.6 7.6 8.2 L8.5 7 L11 7.5 L11 9.5 C11 10.4 10.4 11 9.5 11 C5 11 1 7 1 2.5 C1 1.6 1.6 1 2.5 1 Z" fill="#9bcb3c"/></svg>
      </p>
      <p class="contact__line">512 004 3721
        <svg class="contact__icon" viewBox="0 0 12 12"><rect x="3" y="0.5" width="6" height="11" rx="1" fill="none" stroke="#9bcb3c" stroke-width="1.3"/><circle cx="6" cy="9.5" r=".8" fill="#9bcb3c"/></svg>
      </p>
      <p class="contact__line">info@velrancomponents-example.co.uk
        <svg class="contact__icon" viewBox="0 0 12 12"><rect x="0.5" y="2.5" width="11" height="7.5" fill="#9bcb3c"/><path d="M0.5 2.5 L6 7 L11.5 2.5" fill="none" stroke="#0a8acb" stroke-width="1"/></svg>
      </p>
      <p class="contact__line">www.velrancomponents-example.co.uk
        <svg class="contact__icon" viewBox="0 0 12 12"><circle cx="6" cy="6" r="5.3" fill="none" stroke="#9bcb3c" stroke-width="1.2"/><ellipse cx="6" cy="6" rx="2.3" ry="5.3" fill="none" stroke="#9bcb3c" stroke-width="1"/><path d="M0.7 6 H11.3" stroke="#9bcb3c" stroke-width="1"/></svg>
      </p>
    </div>

    <address class="address">
      17 Marlow Yard, Upper Heath<br>
      Warwick, CV31 8QL<br>
      United Kingdom
    </address>
  </section>

</main>
</body>
</html>
```